Harbor Ridge Painting Epoxy Flyer

We need a promotional flyer for a new epoxy floor coatings division of our painting company. We do epoxy garage floor coatings and paver sealing. It needs to be based on and very similar to the attached flyer. The garage floor picture needs to look more realistic, and the before and after pavers pictures should look less shiny but still a good contrast. Include attached logo

```html
<!DOCTYPE html>
<html lang="en">
<head>
<meta charset="utf-8">
<title>Harbor Ridge Painting – Garage &amp; Driveway Flyer</title>
<link rel="stylesheet" href="https://fonts.googleapis.com/css2?family=Oswald:wght@500;600&family=Roboto+Condensed:ital,wght@0,400;0,500;1,400&family=Playfair+Display:ital,wght@1,700&family=Archivo:wght@700&display=swap">
<style>
  :root {
    --paper: #f6f7f8;
    --ink: #111111;
    --navy: #0b2a6b;
    --blue: #083e96;
    --green: #3c8d16;
    --green-bright: #259a0a;
    --green-dark: #00482a;
    --white: #ffffff;
    --concrete: #8c8574;
    --epoxy: #7d8084;
    --paver-dull: #6d5d52;
    --paver-warm: #9a6a48;
  }
  * { box-sizing: border-box; margin: 0; padding: 0; }
  html, body { width: 970px; height: 1200px; overflow: hidden; }
  body { background: var(--paper); position: relative; font-family: "Roboto Condensed", sans-serif; color: var(--ink); }

  .corner-block { position: absolute; }
  .corner-block--green { left: 826px; top: 0; width: 49px; height: 54px; background: var(--green-bright); }
  .corner-block--dark { left: 875px; top: 0; width: 95px; height: 54px; background: var(--green-dark); }
  .corner-block--blue { left: 875px; top: 54px; width: 95px; height: 45px; background: var(--blue); }

  .brand { position: absolute; left: 57px; top: 100px; display: flex; align-items: center; gap: 12px; }
  .brand__dot { width: 38px; height: 38px; border-radius: 50%; background: var(--green); }
  .brand__name { font-family: "Oswald", sans-serif; font-weight: 600; font-size: 30px; color: var(--navy); text-transform: uppercase; letter-spacing: .5px; white-space: nowrap; }

  .headline { position: absolute; left: 424px; top: 38px; font-family: "Oswald", sans-serif; font-weight: 600; line-height: 1; }
  .headline__top { display: block; font-size: 70px; color: var(--ink); letter-spacing: -.5px; }
  .headline__bottom { display: block; font-size: 70px; margin-top: 4px; letter-spacing: -.5px; white-space: nowrap; }
  .headline__garage { color: var(--blue); }
  .headline__drive { color: var(--green); }

  .tagline { position: absolute; left: 433px; top: 195px; width: 412px; height: 36px; background: var(--navy);
    clip-path: polygon(0 0, 100% 0, 96% 100%, 0 100%); color: var(--white);
    font-family: "Playfair Display", serif; font-style: italic; font-weight: 700; font-size: 25px; line-height: 36px; padding-left: 16px; }

  .photo { position: absolute; }
  .photo--garage-before { left: 47px; top: 290px; width: 242px; height: 475px; background: linear-gradient(180deg, #d8d2c4 0%, #b5ad9c 12%, var(--concrete) 45%, #a59d8c 100%); }
  .photo--garage-after { left: 298px; top: 290px; width: 243px; height: 475px; background: linear-gradient(180deg, #d9d4c6 0%, #b9b5ad 12%, var(--epoxy) 40%, #6a6d72 100%); }
  .photo--paver-before { left: 47px; top: 858px; width: 242px; height: 245px; background: linear-gradient(180deg, #8d7a63 0%, #6f5e4e 22%, var(--paver-dull) 60%, #5d5048 100%); }
  .photo--paver-after { left: 298px; top: 858px; width: 243px; height: 245px; background: linear-gradient(180deg, #8e7760 0%, #8c6143 22%, var(--paver-warm) 60%, #835739 100%); }

  .state-tag { position: absolute; top: 858px; width: 103px; height: 29px; color: var(--white);
    font-family: "Archivo", sans-serif; font-weight: 700; font-size: 18px; line-height: 29px; text-align: center; }
  .state-tag--before { left: 186px; background: var(--navy); }
  .state-tag--after { left: 298px; background: var(--green); }

  .service { position: absolute; left: 577px; }
  .service--epoxy { top: 284px; }
  .service--paver { top: 475px; }
  .service__title { font-family: "Oswald", sans-serif; font-weight: 500; font-size: 28px; line-height: 34px; letter-spacing: .3px; border-left: 3px solid currentColor; padding-left: 8px; margin-bottom: 6px; }
  .service--epoxy .service__title { color: var(--blue); }
  .service--paver .service__title { color: var(--green); }
  .service__list { list-style: none; margin-left: 6px; }
  .service__list li { display: flex; align-items: center; gap: 6px; font-size: 19.5px; line-height: 30px; color: #1a1a1a; white-space: nowrap; }
  .service__list svg { width: 17px; height: 17px; flex: none; }

  .trust-panel { position: absolute; left: 549px; top: 672px; width: 381px; height: 320px; background: var(--blue); color: var(--white); }
  .trust-panel__heading { margin-top: 18px; text-align: center; font-family: "Oswald", sans-serif; font-weight: 500; font-size: 21px; line-height: 27px; }
  .trust-panel__rule { position: absolute; left: 17px; top: 88px; width: 352px; height: 10px; }
  .trust-item { position: absolute; top: 120px; width: 120px; text-align: center; }
  .trust-item svg { width: 82px; height: 82px; display: block; margin: 0 auto 8px; }
  .trust-item span { display: block; font-size: 16px; line-height: 21px; }
  .trust-item--licensed { left: 8px; }
  .trust-item--family { left: 132px; }
  .trust-item--area { left: 260px; }

  .cta { position: absolute; left: 47px; top: 1002px; width: 882px; height: 153px; background: var(--green); color: var(--white); }
  .cta__label { position: absolute; left: 51px; top: 22px; font-family: "Oswald", sans-serif; font-weight: 500; font-size: 33px; line-height: 40px; }
  .cta__icon { position: absolute; left: 50px; top: 75px; width: 54px; height: 54px; }
  .cta__phone { position: absolute; left: 111px; top: 66px; font-family: "Archivo", sans-serif; font-weight: 700; font-size: 67px; line-height: 72px; letter-spacing: -1px; }
  .cta__divider { position: absolute; left: 602px; top: 73px; height: 56px; border-left: 2px dashed rgba(255,255,255,.8); }
  .cta__promise { position: absolute; left: 627px; top: 72px; font-style: italic; font-size: 26px; line-height: 28px; }
</style>
</head>
<body>
  <div class="corner-block corner-block--green"></div>
  <div class="corner-block corner-block--dark"></div>
  <div class="corner-block corner-block--blue"></div>

  <div class="brand">
    <span class="brand__dot"></span>
    <span class="brand__name">Harbor Ridge Painting</span>
  </div>

  <h1 class="headline">
    <span class="headline__top">Upgarde Your</span>
    <span class="headline__bottom"><span class="headline__garage">Garage &amp;</span> <span class="headline__drive">Driveway</span></span>
  </h1>
  <p class="tagline">From worn-out to like new</p>

  <div class="photo photo--garage-before" role="img" aria-label="Worn, stained concrete garage floor before coating"></div>
  <div class="photo photo--garage-after" role="img" aria-label="Garage floor with grey flake epoxy coating after"></div>
  <div class="photo photo--paver-before" role="img" aria-label="Faded brick paver patio before sealing"></div>
  <div class="photo photo--paver-after" role="img" aria-label="Restored warm-toned brick paver patio after sealing"></div>
  <div class="state-tag state-tag--before">BEFORE</div>
  <div class="state-tag state-tag--after">AFTER</div>

  <section class="service service--epoxy">
    <h2 class="service__title">EPROXY FLOOR COATINGS</h2>
    <ul class="service__list">
      <li><svg viewBox="0 0 20 20"><circle cx="10" cy="10" r="8.5" fill="none" stroke="var(--blue)" stroke-width="1.8"/><path d="M6 10.2l2.8 2.8 5.4-5.6" fill="none" stroke="var(--blue)" stroke-width="2"/></svg>Durable, long-lasting finish</li>
      <li><svg viewBox="0 0 20 20"><circle cx="10" cy="10" r="8.5" fill="none" stroke="var(--blue)" stroke-width="1.8"/><path d="M6 10.2l2.8 2.8 5.4-5.6" fill="none" stroke="var(--blue)" stroke-width="2"/></svg>Slip-resistant texture</li>
      <li><svg viewBox="0 0 20 20"><circle cx="10" cy="10" r="8.5" fill="none" stroke="var(--blue)" stroke-width="1.8"/><path d="M6 10.2l2.8 2.8 5.4-5.6" fill="none" stroke="var(--blue)" stroke-width="2"/></svg>Covers cracks &amp; imperfections</li>
      <li><svg viewBox="0 0 20 20"><circle cx="10" cy="10" r="8.5" fill="none" stroke="var(--blue)" stroke-width="1.8"/><path d="M6 10.2l2.8 2.8 5.4-5.6" fill="none" stroke="var(--blue)" stroke-width="2"/></svg>Easy to clean &amp; maintain</li>
    </ul>
  </section>

  <section class="service service--paver">
    <h2 class="service__title">PAVER SEALING</h2>
    <ul class="service__list">
      <li><svg viewBox="0 0 20 20"><circle cx="10" cy="10" r="8.5" fill="none" stroke="var(--green)" stroke-width="1.8"/><path d="M6 10.2l2.8 2.8 5.4-5.6" fill="none" stroke="var(--green)" stroke-width="2"/></svg>Restores color &amp; enhances appearance</li>
      <li><svg viewBox="0 0 20 20"><circle cx="10" cy="10" r="8.5" fill="none" stroke="var(--green)" stroke-width="1.8"/><path d="M6 10.2l2.8 2.8 5.4-5.6" fill="none" stroke="var(--green)" stroke-width="2"/></svg>Protects from sun fading</li>
      <li><svg viewBox="0 0 20 20"><circle cx="10" cy="10" r="8.5" fill="none" stroke="var(--green)" stroke-width="1.8"/><path d="M6 10.2l2.8 2.8 5.4-5.6" fill="none" stroke="var(--green)" stroke-width="2"/></svg>Helps prevent weeds &amp; sand loss</li>
      <li><svg viewBox="0 0 20 20"><circle cx="10" cy="10" r="8.5" fill="none" stroke="var(--green)" stroke-width="1.8"/><path d="M6 10.2l2.8 2.8 5.4-5.6" fill="none" stroke="var(--green)" stroke-width="2"/></svg>Easier to clean &amp; maintain</li>
    </ul>
  </section>

  <section class="trust-panel">
    <h2 class="trust-panel__heading">Practical upgardes that protect<br>and improve your home</h2>
    <svg class="trust-panel__rule" viewBox="0 0 352 10"><path d="M0 1h168l8 7 8-7h168" fill="none" stroke="var(--white)" stroke-width="1.2"/><path d="M168 1l8 7 8-7z" fill="var(--white)"/></svg>

    <div class="trust-item trust-item--licensed">
      <svg viewBox="0 0 82 82" fill="none" stroke="var(--white)" stroke-width="1.8"><circle cx="41" cy="41" r="39"/><path d="M41 19l17 6v13c0 12-8 20-17 24-9-4-17-12-17-24V25z"/><path d="M41 25l11 4v9c0 9-5 14-11 17-6-3-11-8-11-17v-9z"/><path d="M34 40l5 5 9-10" stroke-width="2.4"/></svg>
      <span>Licensed &amp;<br>Insured</span>
    </div>
    <div class="trust-item trust-item--family">
      <svg viewBox="0 0 82 82" fill="none" stroke="var(--white)" stroke-width="1.8"><circle cx="41" cy="41" r="39"/><path d="M24 55l22-22a7 7 0 1 1 5-5l-22 22a4 4 0 1 1-5 5z"/><path d="M58 55L36 33l-4-8-6-4-3 3 4 6 8 4 22 22a3 3 0 1 0 4-4z" transform="translate(-2 0)"/></svg>
      <span>Family-Owned<br>Local<br>Business</span>
    </div>
    <div class="trust-item trust-item--area">
      <svg viewBox="0 0 82 82" fill="none" stroke="var(--white)" stroke-width="1.8"><circle cx="41" cy="41" r="39"/><path d="M41 50c-7-9-11-15-11-21a11 11 0 0 1 22 0c0 6-4 12-11 21z"/><circle cx="41" cy="29" r="4.5"/><path d="M27 48l-5 10h38l-5-10M24 54h34"/></svg>
      <span>Serving<br>Prescott &amp;<br>Surrounding<br>Areas</span>
    </div>
  </section>

  <section class="cta">
    <p class="cta__label">CALL FOR A FREE EXTIMATE</p>
    <svg class="cta__icon" viewBox="0 0 54 54" fill="none" stroke="var(--white)" stroke-width="2.4" stroke-linecap="round"><path d="M14 6l8 10-5 6c3 7 8 12 15 15l6-5 10 8-4 7c-18 2-37-17-35-35z"/><path d="M32 10a13 13 0 0 1 12 12M32 3a20 20 0 0 1 19 19"/></svg>
    <p class="cta__phone">928-555-0147</p>
    <span class="cta__divider"></span>
    <p class="cta__promise">Fast, professional<br>service you can trust</p>
  </section>
</body>
</html>
```